2 x Digitize Logo | 2 x Business Cards | 2 x Fridge Magnets

We require 6 deliverables:
1. Residential logo redrawn (same just high quality for large print format).
2. Corporate logo redrawn (minor changes to wording and high quality for large print format).
3. New business card design for Furniture Removals (residential)
4. New business card design for Corporate Relocations (business)
5. New Fridge magnet for Furniture removals (residential)
6. New fridge magnet for Corporate Relocations (business)
1. Residential Logo
a. We require the logo to be translated into a high quality digital image with no modifications.
(see attached resilogo.jpg)
2. Residential Logo
a. We require the logo to be edited (add the word corporate relocations) be translated into a high quality digital image.
(see attached corplogo.jpg)
3. Using the resilogo please make a new business card for our business.
a. Please see the web site https://www.larkbendcarters.com.au for colours and inspiration.
b. The residential business card needs the following information:
i. Business Name (using the residential logo).
ii. Free Call: 1800 LB Cart (the L, B and Cart much be the same colour as the logo).
iii. Website: www.LarkbendCarters.com.au
iv. Address: 4/17 Ormsdale Court, VIC 3264
v. Email: cart@LarkbendCarters.com.au
vi. backof Card:
Review our service
www.PennantOrbit.com.au
Services: Local, Country, Interstate | Furniture Removals | Piano, Billiard Tables & Antiques
4. Using the corplogo please make a new business card for our business.
b. The corporate business card needs the following information:
i. Business Name (using the corporate logo).
v. Email: corporate@LarkbendCarters.com.au
vi. Back of Card:
Review our service
www.PennantOrbit.com.au
Services: Corporate relocations | Office equipment moves | Packing Service | Packing Materials
5. Using the resilogo please make a new fridge magent for our business.
b. The residential fidge magnet needs the following information:
iv. Services: Local, Country, Interstate | Furniture Removals | Piano, Billiard Tables & Antiques
6. Using the corplogo please make a new fridge magent for our business.
b. The corporate fidge magnet needs the following information:
iv. Services: Local, Country, Interstate | Corporate relocations
Target Market(s)
Residential Furniture Removals and Corporate Office relocations
Industry/Entity Type
Business
Contact Information for Business Card
Please see full brief for six items required
Requirements
Must have
- Clean simple, easy to read
Nice to have
- fresh, stand out, eye catching
Should not have
- plain, standard, boring, general

```html
<!DOCTYPE html>
<html lang="en">
<head>
<meta charset="utf-8">
<title>Larkbend Carters – Corporate Business Card</title>
<link rel="stylesheet" href="https://fonts.googleapis.com/css2?family=Open+Sans:wght@400;600;700&display=swap">
<style>
  :root {
    --backdrop: #121212;
    --card-white: #ffffff;
    --brand-red: #c0120c;
    --brand-green: #00773a;
    --ink: #222222;
    --ink-soft: #555555;
    --on-green: #ffffff;
  }
  * { box-sizing: border-box; margin: 0; padding: 0; }
  html, body {
    width: 1200px; height: 900px; overflow: hidden;
    background: var(--backdrop);
    font-family: "Open Sans", Arial, sans-serif;
  }
  .stage { position: relative; width: 1200px; height: 900px; }

  .card { position: absolute; top: 306px; overflow: hidden; }
  .card--front { left: 149px; width: 439px; height: 271px; background: var(--card-white); }
  .card--back { left: 608px; width: 441px; height: 272px; background: var(--brand-green); color: var(--on-green); }

  .card__art { position: absolute; inset: 0; }

  .free-call {
    position: absolute; left: 40px; top: 30px;
    font-size: 17px; font-weight: 600; color: var(--ink-soft); white-space: nowrap;
  }
  .free-call strong { color: var(--ink); font-weight: 700; }
  .free-call .red { color: var(--brand-red); }
  .free-call .green { color: var(--brand-green); }

  .brand {
    position: absolute; left: 238px; top: 96px;
    display: flex; align-items: center; gap: 6px;
  }
  .brand__mark { width: 9px; height: 9px; background: var(--brand-red); }
  .brand__name {
    font-size: 14px; font-weight: 700; color: var(--brand-green);
    letter-spacing: 0.2px; white-space: nowrap;
  }

  .contacts {
    position: absolute; left: 22px; top: 163px; list-style: none;
    font-size: 14px; color: var(--ink);
  }
  .contacts li { display: flex; align-items: center; gap: 6px; height: 20px; }
  .contacts li + li { margin-top: 2px; }
  .contacts li.address { margin-top: 4px; }
  .contacts svg { width: 10px; height: 10px; flex: none; }

  .review { position: absolute; left: 32px; top: 52px; text-align: center; width: 176px; }
  .review__brand { font-size: 15px; font-weight: 700; letter-spacing: 0.3px; margin-bottom: 12px; }
  .review__label { font-size: 12px; }
  .review__url { font-size: 14px; margin-top: -2px; margin-left: -12px; white-space: nowrap; }

  .services { position: absolute; left: 192px; top: 145px; width: 180px; text-align: center; }
  .services__title {
    display: flex; align-items: center; justify-content: center; gap: 4px;
    font-size: 12px; margin-bottom: 10px;
  }
  .services__title::before, .services__title::after {
    content: ""; width: 36px; height: 1px; background: var(--on-green);
  }
  .services__list { list-style: none; font-size: 12px; line-height: 16px; text-transform: uppercase; }
</style>
</head>
<body>
<main class="stage">

  <section class="card card--front" aria-label="Business card front">
    <svg class="card__art" viewBox="0 0 439 271" aria-hidden="true">
      <polygon points="0,23 14,23 21,61 0,61" fill="var(--brand-red)"/>
      <polygon points="14,23 33,23 33,61 21,61" fill="var(--brand-green)"/>
      <polygon points="0,251 237,251 222,271 0,271" fill="var(--brand-red)"/>
      <polygon points="250,244 439,244 439,271 223,271" fill="var(--brand-green)"/>
    </svg>

    <p class="free-call">Free Call: <strong>1800 <span class="red">L</span><span class="green">B</span> <span class="red">Cart</span></strong></p>

    <div class="brand">
      <span class="brand__mark"></span>
      <span class="brand__name">LARKBEND CARTERS</span>
    </div>

    <ul class="contacts">
      <li>
        <svg viewBox="0 0 10 10"><rect x="0" y="2" width="10" height="7" fill="var(--brand-red)"/><polyline points="0,2 5,6 10,2" fill="none" stroke="#fff" stroke-width="1"/></svg>
        corporate@LarkbendCarters.com.au
      </li>
      <li>
        <svg viewBox="0 0 10 10"><circle cx="5" cy="5" r="4.5" fill="var(--brand-red)"/><path d="M2 4 Q4 3 5 5 T8 6" fill="none" stroke="#fff" stroke-width="1"/></svg>
        www.LarkbendCarters.com.au
      </li>
      <li class="address">
        <svg viewBox="0 0 10 12" style="height:12px"><path d="M5 0 A4 4 0 0 1 9 4 C9 7 5 12 5 12 C5 12 1 7 1 4 A4 4 0 0 1 5 0 Z" fill="var(--brand-red)"/><circle cx="5" cy="4" r="1.5" fill="#fff"/></svg>
        4/17 Ormsdale Court, VIC 3264
      </li>
    </ul>
  </section>

  <section class="card card--back" aria-label="Business card back">
    <div class="review">
      <p class="review__brand">LARKBEND CARTERS</p>
      <p class="review__label">Review our service</p>
      <p class="review__url">www.PennantOrbit.com.au</p>
    </div>

    <div class="services">
      <p class="services__title">SERVICES</p>
      <ul class="services__list">
        <li>Corporate Relocations</li>
        <li>Office Equipment Moves</li>
        <li>Packing Service</li>
        <li>Packing Materials</li>
      </ul>
    </div>
  </section>

</main>
</body>
</html>
```